Meadowlight Soaps Business Card

The new business card design will incorporate my new logo components designed by one of your designers. Meadowlight Soaps creates high quality soaps and bath products. They would be suited for a Spa, Bed and Breakfast, Boutique environment. The look should be a white background.
Classy, soft and using the colour palet of the logo. The card will be two sided.

Reason: Need more time to make some changes and decide.

Target Market(s)

Looking to appeal to an upper end market. Spas, boutiques, independent gift stores, bridal salons, bed and breakfast, etc. I want the card to impart a sense of elegance, tranquility and Meadowlight. But also quality and value.

Industry/Entity Type

Business

Font styles to use
Sans Serif
Script

Requirements
Must have
• My logo on the front. But also on the back but faded out to allow written notes on the back.
On the front : Carol Pritchett
Owner/Creator
48 Fenwick Rd
Guelph, Ont N4K 2P9
519.402.6183
Creating Quality Handcrafted Soaps And Bath Products
Custom and Wholesale Orders Welcome
Www.meadowlightsoaps.ca
Www.facebook.com / MeadowlightSoapandBath
info@meadowlightsoaps.ca

```html
<!DOCTYPE html>
<html lang="en">
<head>
<meta charset="utf-8">
<title>Meadowlight Soaps Business Card</title>
<link href="https://fonts.googleapis.com/css2?family=Lato:wght@400;700&family=Pinyon+Script&display=swap" rel="stylesheet">
<style>
  :root {
    --backdrop: #ececea;
    --card: #ffffff;
    --sage: #8fb3aa;
    --sage-band: #9bbbb3;
    --swoosh: #cbc8c9;
    --text-grey: #b3b3b3;
    --faint-sage: #e6eeec;
  }
  html, body {
    margin: 0;
    padding: 0;
    width: 1200px;
    height: 1000px;
    overflow: hidden;
    background: var(--backdrop);
  }
  .canvas {
    position: relative;
    width: 1200px;
    height: 1000px;
  }
  .card {
    position: absolute;
    top: 156px;
    width: 402px;
    height: 687px;
    background: var(--card);
    overflow: hidden;
    box-shadow: 0 3px 10px rgba(0,0,0,0.18);
    font-family: "Lato", Arial, sans-serif;
    text-align: center;
  }
  .card--front { left: 139px; }
  .card--back { left: 645px; }
  .card__waves {
    position: absolute;
    left: 0;
    top: 0;
    width: 402px;
    height: 687px;
  }
  .brand-mark {
    position: absolute;
    left: 151px;
    top: 70px;
    width: 100px;
    height: 100px;
    border-radius: 50%;
    background: var(--sage);
    opacity: 0.85;
  }
  .brand-name {
    position: absolute;
    left: 0;
    right: 0;
    top: 232px;
    font-size: 34px;
    font-weight: 400;
    color: var(--sage);
    letter-spacing: 1px;
  }
  .owner-name {
    position: absolute;
    left: 0;
    right: 0;
    top: 335px;
    font-family: "Pinyon Script", cursive;
    font-size: 40px;
    color: var(--sage);
    line-height: 1;
  }
  .owner-role {
    position: absolute;
    left: 0;
    right: 0;
    top: 386px;
    font-size: 16px;
    font-weight: 700;
    color: var(--text-grey);
  }
  .address {
    position: absolute;
    left: 0;
    right: 0;
    top: 420px;
    font-size: 19px;
    line-height: 27px;
    color: var(--text-grey);
  }
  .contacts {
    position: absolute;
    left: 96px;
    top: 486px;
    margin: 0;
    padding: 0;
    list-style: none;
    text-align: left;
    font-size: 15px;
    font-weight: 700;
    color: var(--text-grey);
    z-index: 1;
  }
  .contacts li {
    display: flex;
    align-items: center;
    height: 26.5px;
  }
  .contacts svg {
    width: 18px;
    height: 18px;
    margin-right: 7px;
    flex: none;
  }
  .contacts li.phone { padding-left: 38px; }
  .dot-icon {
    width: 11px;
    height: 11px;
    border-radius: 50%;
    background: var(--sage);
    margin: 0 10px 0 4px;
    flex: none;
  }
  .notes-title {
    position: absolute;
    left: 0;
    right: 0;
    top: 70px;
    font-family: "Pinyon Script", cursive;
    font-size: 64px;
    color: var(--sage);
    line-height: 1;
  }
  .faded-mark {
    position: absolute;
    left: 76px;
    top: 170px;
    width: 250px;
    height: 250px;
    border-radius: 50%;
    background: var(--faint-sage);
  }
  .tagline {
    position: absolute;
    left: 0;
    right: 0;
    top: 484px;
    font-size: 17.5px;
    font-weight: 700;
    line-height: 26.5px;
    color: var(--text-grey);
    z-index: 1;
  }
</style>
</head>
<body>
<div class="canvas">

  <section class="card card--front">
    <svg class="card__waves" viewBox="0 0 402 687" aria-hidden="true">
      <path d="M0,534 C0,595 40,605 362,598 C240,622 80,610 0,578 Z" fill="var(--swoosh)"/>
      <path d="M0,592 C80,650 250,660 402,582 L402,687 L0,687 Z" fill="var(--sage-band)"/>
    </svg>
    <div class="brand-mark" aria-hidden="true"></div>
    <div class="brand-name">Meadowlight Soaps</div>
    <div class="owner-name">Carol Pritchett</div>
    <div class="owner-role">Owner</div>
    <div class="address">48 Fenwick Rd,<br>Guelph, Ont N4K 2P9</div>
    <ul class="contacts">
      <li class="phone">
        <svg viewBox="0 0 20 20" aria-hidden="true"><path d="M5 2 L8 2 L9 6 L7 8 C8 11 10 13 12 14 L14 12 L18 13 L18 16 C18 17 17 18 16 18 C9 18 2 11 2 4 C2 3 3 2 5 2 Z" fill="var(--sage)"/></svg>
        519.402.6183
      </li>
      <li>
        <svg viewBox="0 0 20 20" aria-hidden="true"><rect x="2" y="4" width="16" height="12" fill="none" stroke="var(--sage)" stroke-width="1.8"/><path d="M2 4 L10 11 L18 4" fill="none" stroke="var(--sage)" stroke-width="1.8"/></svg>
        info@meadowlightsoaps.ca
      </li>
      <li>
        <svg viewBox="0 0 20 20" aria-hidden="true"><circle cx="10" cy="10" r="8" fill="none" stroke="var(--sage)" stroke-width="1.8"/><ellipse cx="10" cy="10" rx="3.5" ry="8" fill="none" stroke="var(--sage)" stroke-width="1.4"/><path d="M2 10 H18" stroke="var(--sage)" stroke-width="1.4"/></svg>
        www.meadowlightsoaps.ca
      </li>
      <li>
        <span class="dot-icon" aria-hidden="true"></span>
        MeadowlightSoapandBath
      </li>
    </ul>
  </section>

  <section class="card card--back">
    <svg class="card__waves" viewBox="0 0 402 687" aria-hidden="true">
      <path d="M0,534 C0,595 40,605 362,598 C240,622 80,610 0,578 Z" fill="var(--swoosh)"/>
      <path d="M0,592 C80,650 250,660 402,582 L402,687 L0,687 Z" fill="var(--sage-band)"/>
    </svg>
    <div class="faded-mark" aria-hidden="true"></div>
    <div class="notes-title">Notes:</div>
    <div class="tagline">
      Creating Quality Handcrafted Soaps<br>
      And Bath Products.<br>
      Custom and Wholesale Orders<br>
      Welcome.
    </div>
  </section>

</div>
</body>
</html>
```